Mobile Repair Service on location needs a Web Design

We are starting a new mobile device repair service called Handset Haven and our website needs a design!

Hello Designers!
First, we'd like to make clear this is more than a simple web design contest, we want the designers to create an idea. We want someone who can create the whole theme of the service's we provide. We want someone that can help design our visual branding, help us communicate a sentiment. And we are willing to pay for that.

Who are we?
Our company is based in Rotterdam, the Netherlands. We provide different services for all kinds of electronic devices. The kind of services we provide are, among other things, installations of hardware and software and the repair of broken or malfunctioning devices.
We are starting a new service that offers mobile device repairs on location, be it at the home of our customers, their office, or any other place. Just give us the address and we will come to you for the repair job. This is also our main USP. We have multiple skilled engineers who drive trough the country on a daily basis and can be on location within a working day. Repair is done immediately onsite while the customer waits. At this stage we will start with the smartphone product-group within the mobile devices. In a second phase we might also add tablets.
People don't want to be without their phone for weeks because of some parts that needed to be ordered by a repair center they had to sent their phone to. We offer a fully functional mobile repair center in the form of specially customized vans. These vans have all the tools and utilities needed by our engineers to safely repair your mobile device. Your phone is being repaired directly in front of you, the next business-day, on a location you desire.

For this new service we are creating a website called Handset Haven. The website needs a story and matching design and this is where you come in. We are not looking for a simple template design we can get from any place. We need a story. We want you to create an idea, build a unique theme or vision that helps sell the product/service. This goes beyond the design of the website. We need the whole package, the design you are creating needs to have returning elements like icons, color use, images, maybe even characters etc. You name it! There needs to be a common thread in the design so we can reuse elements in, for example, the email templates, the work order or receipt we give to our customers (we may contact the winner of the contest to design these for us as well!).

The name 'Handset Haven' is chosen. Rehab (short for rehabilitate) has a bold and playful tone to it and the design needs to reflect the name. So we're looking for a somewhat playful and cheeky design. Definitely not too serious and definitely modern. We already got a logo that we love and that fit's this description (see attached design documents for the logo). It's bold, powerful and fun. Our web design needs to reflect this as well and has to fit in with our logo.
We would really like it if the design somehow incorporates elements that highlight our unique selling points (repairs on location, we come to you etc.). We would really like some form of story telling in the design. Think clumsy people breaking their phones. Teenagers in tears because they have no access to their friends. People nowadays have the need to always be 'connected'. What happens when your phone is broken or malfunctioning? We're handling tech, we are nerds and a little bit weird, but we're professionals and here to help you with your problem. The sentiment Byte Brigade tries to communicate is something we really like. We're looking for fresh idea's, anything goes!

In an overview all Unique Selling Points of the Handset haven service:
- Professional service on location. Don’t ship to us we will come to you!
- Clear pricing upfront. No hidden cost.
- Next business-day repair.
- Backed by a professional call center open 12 hours a day and open on a Saturday as well
- Backed by a professional repair center with more then 12 years of experience
- Repair is done by certified engineers
- 1 year warranty on the repair

The process:
The main function of our website will be for customers to make a repair request. A customer will visit our website and can make a repair request immediately by going through a 'request-order-flow'. In this flow he or she will need to fill in some forms and can select wich type/model/brand of mobile device he or she has and what parts need to be repaired. After a request is placed we will call the customer back (within an hour) for a short intake and to set a date/time and location. Our engineer will meet the customer at the specified location and will repair the device onsite in one of our mobile repair centers, which is a specialized van equipped with all the tools needed for device restorations.
So in short the steps are:
- Choose your device and repair job
- Place the order
- Get a callback within the hour
- Set date and location
- We will come to you.

Website functionality:
Our website is our main form of communication. So the sentiment we want to communicate needs be reflected in the design. We need a main/front page designed (preferably a long scrolling page design) containing:
1. Customers will be able to request a repair job directly on our website. So there will need to be a prominent button/link at the top of our main page that will bring the customer to this 'request-order-flow'. This is the main flow which needs to be full focus on the front page. All other items are secondary.
2. The general information of who we are and what we do, and why the customer should choose us. Preferably in short bullet-point type keywords/sentences with icons or other visual cues. See our unique selling points to get an idea of the information that will be displayed here.
3. There needs to be a section that will explain the process (see above) of a repair request step-by- step, again in brief short key sentences and with (custom) icons.
4. There needs to be a section that explains to the customer he/she can always contact us if they are not sure what the problem is with their device, and for this reason are not sure what repair request they should order.
5. We want to implement some functionality that display customer ratings or customer reviews. So there needs to be room for some kind of widget of plugin we're going to implement which shows these reviews.
6. A 'For business section' where we will explain all the options we provide for corporate clients.
7. Social media links.
8. There needs to be a menu with buttons that leads to the all sections described in the previous points.

For now, we need a design for our front page. In the second phase, when we have picked our winner, we may ask the winner to design the page(s) for our request workflow as well.

EDIT:
Finally, we have a very specific order in mind for the different segments of our website. We would like you to add some more segments that were not in our original brief as well:

1. Top header with order/request button. (should instantly make clear our main USP, we do repairs on location)
2. Our process
3. Our unique selling points / why choose us
4. The kind of repairs we do (broken screens, broken batteries, water damage, broken camera's, no sound etc.)
5. A 'meet our team' section, where we introduce some of our engineers
6. A 'contact us for any questions' section/
7. Testimonials/user reviews
8. A section where we show key performance indicators
9. 'For businesses' sections
10.'Subscribe for newsletter' field
11. Social media buttons

Industry/Entity Type

It Service

Number of Pages Required

1 page

Font styles to use
Sans Serif

Requirements
Must have
• a main/front page, design only
• custom icons/images for banners, adverts online and in print (high res)
Nice to have
• Storytelling in our design.
• Design that fits with our brand new logo.
• Elements like icons to have a flat design.
• Keep in mind that the website will need to be responsive when designing! (Ideally provide an example of the mobile design as well)
• Create a fun and trustworthy feeling.

```html
<!DOCTYPE html>
<html lang="en">
<head>
<meta charset="utf-8">
<title>Handset Haven – We will come to you</title>
<link rel="stylesheet" href="https://fonts.googleapis.com/css2?family=Roboto:wght@300;400;500;700&display=swap">
<style>
:root{
  --orange:#f15a22;
  --orange-dark:#e24f17;
  --ink:#333438;
  --text:#555;
  --muted:#8a8a8a;
  --line:#d9d9d9;
  --panel:#f4f4f5;
  --footer:#f3f3f5;
  --white:#fff;
}
*{box-sizing:border-box;margin:0;padding:0}
html,body{width:1200px;height:2359px;overflow:hidden}
body{font-family:'Roboto',Arial,sans-serif;color:var(--text);background:var(--white);position:relative}
.abs{position:absolute}

/* header */
.top-line{left:0;top:0;width:1200px;height:4px;background:var(--orange)}
.callbar{left:708px;top:0;width:492px;height:44px;background:var(--orange);clip-path:polygon(0 0,100% 0,100% 100%,26px 100%)}
.callbar .call{position:absolute;left:62px;top:13px;color:var(--white);font-size:14px;font-weight:500;display:flex;align-items:center;gap:12px}
.callbar .socials{position:absolute;right:22px;top:9px;display:flex;gap:5px}
.callbar .socials span{width:25px;height:25px;border:1.5px solid var(--white);border-radius:50%}
.brand{left:86px;top:28px;display:flex;align-items:center;gap:12px}
.brand .mark{width:44px;height:44px;border-radius:50%;background:var(--orange)}
.brand .name{font-weight:500;font-size:24px;color:var(--ink)}
.nav-link{top:69px;font-size:11.5px;color:var(--ink);text-decoration:none}
.nav-link.active{color:var(--orange)}
.nav-sep{left:1080px;top:68px;width:1px;height:14px;background:var(--line)}
.nav-search{left:1092px;top:69px}
.header-shadow{left:0;top:104px;width:1200px;height:1px;background:#e6e6e6}

/* hero */
.hero{left:0;top:105px;width:1200px;height:474px;background:linear-gradient(90deg,#efefef,#e6e6e6)}
.hero-photo{left:456px;top:105px;width:744px;height:474px;background:radial-gradient(ellipse at 55% 45%,#f6f6f6 0%,#e3e3e3 70%,#dcdcdc 100%)}
.hero-title{left:86px;top:203px;font-size:44px;font-weight:400;color:var(--ink)}
.hero-sub{left:86px;top:260px;font-size:37px;font-weight:300;color:var(--orange)}
.hero-text{left:86px;top:321px;width:402px;font-size:12px;line-height:27px;color:var(--ink)}
.btn-solid{left:86px;top:425px;width:206px;height:39px;background:var(--orange);color:var(--white);font-size:14px;font-weight:500;display:flex;align-items:center;justify-content:center;border-radius:2px}
.dots{left:86px;top:548px;display:flex;gap:3px}
.dots span{width:14px;height:14px;border:1.5px solid #999;border-radius:50%}
.dots span.on{border-color:var(--orange)}

/* process */
.section-title{font-size:25px;font-weight:400;color:var(--orange)}
.process-title{left:0;width:1200px;top:630px;text-align:center}
.process-sub{left:0;width:1200px;top:676px;text-align:center;font-size:12px;color:var(--muted)}
.step{top:747px;width:200px;text-align:center}
.step .ring{width:114px;height:114px;border:1.5px solid #cfcfcf;border-radius:50%;margin:0 auto;display:flex;align-items:center;justify-content:center}
.step.active .ring{border-color:var(--orange)}
.step p{margin-top:20px;font-size:12.5px;line-height:22px;color:#666;font-weight:500}
.step.active p{color:var(--orange)}
.arrow{top:795px}

/* usp */
.usp-photo{left:0;top:991px;width:500px;height:374px;background:linear-gradient(135deg,#6b6f77 0%,#3d4451 45%,#b8b9bc 100%)}
.usp-panel{left:500px;top:991px;width:700px;height:374px;background:var(--panel)}
.usp-title{left:547px;top:1026px}
.usp-list{left:551px;top:1085px;list-style:none}
.usp-list li{display:flex;align-items:center;gap:16px;height:37.7px;font-size:12.5px;color:#555}

/* about + customers */
.about-title{left:86px;top:1408px}
.about-text{left:86px;top:1462px;width:372px;font-size:12px;line-height:23px;color:#555}
.btn-outline{width:126px;height:39px;border:1.5px solid var(--orange);color:var(--orange);font-size:13px;font-weight:500;display:flex;align-items:center;justify-content:center;border-radius:2px}
.about-btn{left:86px;top:1625px}
.customers-title{left:519px;top:1408px}
.avatar{left:519px;top:1466px;width:126px;height:126px;border-radius:50%;background:radial-gradient(circle at 50% 45%,#c99a7e 0%,#7a5641 60%,#3e2d25 100%)}
.quote-open{left:664px;top:1474px;font-size:30px;color:#555;font-family:Georgia,serif}
.quote-close{left:990px;top:1574px;font-size:30px;color:#555;font-family:Georgia,serif}
.quote-text{left:684px;top:1494px;width:420px;font-size:12px;line-height:22.5px;color:#555}
.review-name{left:684px;top:1612px;font-size:13.5px;font-weight:500;color:var(--orange)}
.review-date{left:684px;top:1636px;font-size:11px;color:var(--muted)}

/* who we are */
.who{left:0;top:1707px;width:1200px;height:325px;background:linear-gradient(135deg,var(--orange) 0%,var(--orange-dark) 100%)}
.who-title{left:0;top:1763px;width:1200px;text-align:center;color:var(--white);font-size:25px;font-weight:400}
.who-text{left:220px;top:1813px;width:760px;text-align:center;color:var(--white);font-size:12.5px;line-height:26.5px}
.who-btn{left:477px;top:1941px;width:246px;height:42px;border:1.5px solid var(--white);color:var(--white);font-size:13px;font-weight:500;display:flex;align-items:center;justify-content:center;border-radius:2px}

/* footer */
.footer{left:0;top:2032px;width:1200px;height:327px;background:var(--footer)}
.foot-brand{left:86px;top:2134px;display:flex;align-items:center;gap:14px}
.foot-brand .mark{width:64px;height:64px;border-radius:50%;background:var(--orange)}
.foot-brand .name{font-size:26px;font-weight:500;color:var(--ink)}
.foot-head{top:2076px;font-size:15.5px;font-weight:400;color:var(--ink)}
.contact-list{left:393px;top:2120px;list-style:none;font-size:12px;color:#666}
.contact-list li{display:flex;gap:12px;align-items:flex-start;height:29px}
.contact-list a{color:#666}
.news-text{left:621px;top:2118px;width:240px;font-size:12px;line-height:21px;color:#777}
.news-input{left:623px;top:2174px;width:211px;height:33px;border:1px solid #ccc;background:var(--white);font-size:12px;color:#555;padding:9px 12px}
.subscribe{left:623px;top:2215px;width:80px;height:28px;background:var(--orange);color:var(--white);font-size:10.5px;font-weight:500;display:flex;align-items:center;justify-content:center}
.follow-text{left:882px;top:2118px;width:230px;font-size:12px;line-height:21px;color:#777}
.follow-icons{left:880px;top:2199px;display:flex;gap:8px}
.follow-icons span{width:35px;height:35px;border:1.5px solid #aaa;border-radius:50%}
.foot-rule{left:86px;top:2284px;width:1024px;height:1px;background:#ddd}
.copyright{left:0;top:2316px;width:1200px;text-align:center;font-size:12px;color:#555}
</style>
</head>
<body>

<!-- header -->
<div class="abs top-line"></div>
<div class="abs callbar">
  <div class="call">
    <svg width="13" height="13" viewBox="0 0 24 24"><path fill="#fff" d="M6.6 10.8a15 15 0 0 0 6.6 6.6l2.2-2.2c.3-.3.7-.4 1-.2 1.1.4 2.3.6 3.6.6.6 0 1 .4 1 1V20c0 .6-.4 1-1 1A17 17 0 0 1 3 4c0-.6.4-1 1-1h3.5c.6 0 1 .4 1 1 0 1.3.2 2.5.6 3.6.1.3 0 .7-.2 1z"/></svg>
    CALL US : (000)-555-0142
  </div>
  <div class="socials"><span></span><span></span><span></span><span></span><span></span></div>
</div>

<div class="abs brand">
  <div class="mark"></div>
  <div class="name">Handset Haven</div>
</div>

<nav>
  <a class="abs nav-link active" style="left:505px" href="#">HOME</a>
  <a class="abs nav-link" style="left:591px" href="#">ABOUT US</a>
  <a class="abs nav-link" style="left:698px" href="#">SERVICES</a>
  <a class="abs nav-link" style="left:802px" href="#">PRODUCTS</a>
  <a class="abs nav-link" style="left:915px" href="#">NEWS</a>
  <a class="abs nav-link" style="left:999px" href="#">CONTACT US</a>
  <span class="abs nav-sep"></span>
  <svg class="abs nav-search" width="12" height="12" viewBox="0 0 24 24"><circle cx="10" cy="10" r="7" fill="none" stroke="#f15a22" stroke-width="3"/><path d="M15 15l7 7" stroke="#f15a22" stroke-width="3"/></svg>
</nav>
<div class="abs header-shadow"></div>

<!-- hero -->
<section class="abs hero"></section>
<div class="abs hero-photo" role="img" aria-label="Hands with tweezers and a screwdriver over a disassembled smartphone and repair tools laid out on a white desk"></div>
<h1 class="abs hero-title">HANDSET HAVEN</h1>
<div class="abs hero-sub">WE WILL COME TO YOU</div>
<p class="abs hero-text">Our company is based in Rotterdam, the Netherlands. We provide different services for all kinds of electronic devices. The kind of we provide installations of hardware &amp; software</p>
<div class="abs btn-solid">REQUEST-ORDER-FLOW</div>
<div class="abs dots"><span></span><span></span><span class="on"></span><span></span><span></span></div>

<!-- process -->
<h2 class="abs section-title process-title">HOW IT WORKS</h2>
<p class="abs process-sub">We are starting a new service that offers mobile device repairs on location, be it at the home of our customers</p>

<div class="abs step active" style="left:92px">
  <div class="ring">
    <svg width="58" height="50" viewBox="0 0 58 50" fill="none" stroke="#f15a22" stroke-width="2.5"><rect x="3" y="3" width="52" height="34" rx="2"/><path d="M22 47h14M29 37v10"/><circle cx="22" cy="20" r="7"/><circle cx="22" cy="20" r="2.5"/><path d="M33 14l12 12M41 14l-8 8"/></svg>
  </div>
  <p>CHOOSE YOUR DEVICE &amp;<br>REPAIR JOB</p>
</div>
<div class="abs step" style="left:298px">
  <div class="ring">
    <svg width="44" height="54" viewBox="0 0 44 54" fill="none" stroke="#888" stroke-width="2.5"><rect x="3" y="6" width="34" height="44" rx="2"/><rect x="13" y="2" width="14" height="8" rx="1"/><path d="M10 20h4M18 20h12M10 29h4M18 29h12M10 38h4M18 38h6"/><circle cx="35" cy="43" r="7" fill="#888"/><path d="M31 43l3 3 5-5" stroke="#fff"/></svg>
  </div>
  <p>PLACE THE<br>ORDER</p>
</div>
<div class="abs step" style="left:504px">
  <div class="ring">
    <svg width="54" height="54" viewBox="0 0 54 54" fill="none" stroke="#888" stroke-width="2.5"><circle cx="30" cy="24" r="18"/><path d="M30 13v11l7 5"/><path d="M8 24c-3 3-3 8 2 14s12 12 17 12c3 0 5-2 6-4l-6-5-4 3c-3-1-7-5-8-8l3-4-5-6z" fill="#888"/></svg>
  </div>
  <p>GET A CALLBACK WITHIN<br>THE HOUR</p>
</div>
<div class="abs step" style="left:710px">
  <div class="ring">
    <svg width="52" height="52" viewBox="0 0 52 52" fill="none" stroke="#888" stroke-width="2.5"><rect x="3" y="7" width="38" height="36" rx="2"/><path d="M3 16h38M12 3v8M32 3v8"/><path d="M10 23h4M18 23h4M26 23h4M10 30h4M18 30h4M10 37h4"/><circle cx="40" cy="40" r="9" fill="#fff"/><path d="M40 33a6 6 0 0 1 6 6c0 5-6 10-6 10s-6-5-6-10a6 6 0 0 1 6-6z" fill="#888"/></svg>
  </div>
  <p>SET DATE AND<br>LOCATION</p>
</div>
<div class="abs step" style="left:916px">
  <div class="ring">
    <svg width="44" height="52" viewBox="0 0 44 52"><path d="M22 2a14 14 0 0 1 14 14c0 11-14 26-14 26S8 27 8 16A14 14 0 0 1 22 2z" fill="#888"/><circle cx="22" cy="16" r="5" fill="#fff"/><ellipse cx="22" cy="47" rx="14" ry="3" fill="#bbb"/></svg>
  </div>
  <p>WE WILL COME<br>TO YOU</p>
</div>

<svg class="abs arrow" style="left:266px" width="56" height="20" viewBox="0 0 56 20" fill="none" stroke="#999" stroke-width="1.2"><path d="M2 14c14-12 34-12 50-2"/><path d="M46 8l6 4-7 2"/></svg>
<svg class="abs arrow" style="left:472px" width="56" height="20" viewBox="0 0 56 20" fill="none" stroke="#999" stroke-width="1.2"><path d="M2 14c14-12 34-12 50-2"/><path d="M46 8l6 4-7 2"/></svg>
<svg class="abs arrow" style="left:678px" width="56" height="20" viewBox="0 0 56 20" fill="none" stroke="#999" stroke-width="1.2"><path d="M2 14c14-12 34-12 50-2"/><path d="M46 8l6 4-7 2"/></svg>
<svg class="abs arrow" style="left:884px" width="56" height="20" viewBox="0 0 56 20" fill="none" stroke="#999" stroke-width="1.2"><path d="M2 14c14-12 34-12 50-2"/><path d="M46 8l6 4-7 2"/></svg>

<!-- usp -->
<div class="abs usp-photo" role="img" aria-label="Engineer in a checked shirt repairing a phone circuit board at a workbench"></div>
<div class="abs usp-panel"></div>
<h2 class="abs section-title usp-title">OUR USP</h2>
<ul class="abs usp-list">
  <li><svg width="12" height="10" viewBox="0 0 12 10"><path d="M1 5l3.5 3.5L11 1" fill="none" stroke="#f15a22" stroke-width="2.2"/></svg>Professional service on location. Don't ship to us we will come to you!</li>
  <li><svg width="12" height="10" viewBox="0 0 12 10"><path d="M1 5l3.5 3.5L11 1" fill="none" stroke="#f15a22" stroke-width="2.2"/></svg>Clear pricing upfront. No hidden cost</li>
  <li><svg width="12" height="10" viewBox="0 0 12 10"><path d="M1 5l3.5 3.5L11 1" fill="none" stroke="#f15a22" stroke-width="2.2"/></svg>Next business-day repair</li>
  <li><svg width="12" height="10" viewBox="0 0 12 10"><path d="M1 5l3.5 3.5L11 1" fill="none" stroke="#f15a22" stroke-width="2.2"/></svg>Backed by a professional call center open 12 hours a day and open on a Saturday as well</li>
  <li><svg width="12" height="10" viewBox="0 0 12 10"><path d="M1 5l3.5 3.5L11 1" fill="none" stroke="#f15a22" stroke-width="2.2"/></svg>Backed by a professional repair center with more then 12 years of experience</li>
  <li><svg width="12" height="10" viewBox="0 0 12 10"><path d="M1 5l3.5 3.5L11 1" fill="none" stroke="#f15a22" stroke-width="2.2"/></svg>Repair is done by certified engineers</li>
  <li><svg width="12" height="10" viewBox="0 0 12 10"><path d="M1 5l3.5 3.5L11 1" fill="none" stroke="#f15a22" stroke-width="2.2"/></svg>1 year warranty on the repair</li>
</ul>

<!-- about -->
<h2 class="abs section-title about-title">ABOUT US</h2>
<p class="abs about-text">People don't want to be without their phone for weeks because of some parts that needed to be ordered by a repair center they had to sent their phone to. We offer a fully functional mobile repair center in the form of specially customized vans. These vans have all the tools and utilities needed by our engineers to safely repair your mobile business-day, on a location you desire.</p>
<div class="abs btn-outline about-btn">READ MORE</div>

<!-- customers -->
<h2 class="abs section-title customers-title">OUR CUSTOMERS</h2>
<div class="abs avatar" role="img" aria-label="Portrait photo of a smiling customer"></div>
<div class="abs quote-open">&ldquo;</div>
<p class="abs quote-text">The kind of services we provide are, among other things, installations of hardware and software and the repair of broken or malfunctioning devices. We are starting a new service that offers mobile device repairs on location, be it at the home of our customers, their office, or any other place.</p>
<div class="abs quote-close">&rdquo;</div>
<div class="abs review-name">Name : Mara Jansen</div>
<div class="abs review-date">Posed on 02 February 2017</div>

<!-- who we are -->
<section class="abs who"></section>
<h2 class="abs who-title">WHO ARE WE</h2>
<p class="abs who-text">We are starting a new service that offers mobile device repairs on location, be it at the home of our customers, their office, or any other place. Just give us the address and we will come to you for the repair job. This is also our main USP. We have multiple skilled engineers who drive trough the country on a daily basis and can be on location within a working day. Repair is done immediately onsite while the customer within the mobile devices. In a second phase we might also add tablets.</p>
<div class="abs who-btn">CLICK HERE FOR MORE INFO</div>

<!-- footer -->
<footer class="abs footer"></footer>
<div class="abs foot-brand">
  <div class="mark"></div>
  <div class="name">Handset Haven</div>
</div>

<h3 class="abs foot-head" style="left:393px">CONTACT US</h3>
<ul class="abs contact-list">
  <li><svg width="13" height="13" viewBox="0 0 24 24"><path fill="#888" d="M6.6 10.8a15 15 0 0 0 6.6 6.6l2.2-2.2c.3-.3.7-.4 1-.2 1.1.4 2.3.6 3.6.6.6 0 1 .4 1 1V20c0 .6-.4 1-1 1A17 17 0 0 1 3 4c0-.6.4-1 1-1h3.5c.6 0 1 .4 1 1 0 1.3.2 2.5.6 3.6.1.3 0 .7-.2 1z"/></svg>(000)-555-0142 &nbsp;(Phone)</li>
  <li><svg width="13" height="13" viewBox="0 0 24 24" fill="#888"><rect x="6" y="2" width="12" height="6"/><rect x="2" y="9" width="20" height="9" rx="1"/><rect x="6" y="15" width="12" height="7"/></svg>(000)-555-0142 &nbsp;(Fax)</li>
  <li><svg width="13" height="13" viewBox="0 0 24 24" fill="none" stroke="#888" stroke-width="2.5"><rect x="2" y="5" width="20" height="14"/><path d="M2 5l10 8 10-8"/></svg><a href="#">info@handsethaven.com</a></li>
  <li><svg width="13" height="13" viewBox="0 0 24 24"><path fill="#888" d="M12 2a7 7 0 0 1 7 7c0 6-7 13-7 13S5 15 5 9a7 7 0 0 1 7-7z"/><circle cx="12" cy="9" r="2.5" fill="#f3f3f5"/></svg><span>245 Lorem Ipsum Ipsum<br>Dummy Text</span></li>
</ul>

<h3 class="abs foot-head" style="left:621px">NEWSLETTER</h3>
<p class="abs news-text">Register Your email address to get information abiout us</p>
<div class="abs news-input">Email Address</div>
<div class="abs subscribe">SUBSCRIBE</div>

<h3 class="abs foot-head" style="left:882px">FOLLOW US</h3>
<p class="abs follow-text">Our company is based in Rotterdam the Netherlands. We provide different services for all kinds</p>
<div class="abs follow-icons"><span></span><span></span><span></span><span></span><span></span></div>

<div class="abs foot-rule"></div>
<p class="abs copyright">© Copyright 2017 Handset Haven.All Rights Reserved</p>

</body>
</html>
```